Halvorsen Construction Needs a Business Card

Our current business card is very bland, and since we have a new logo, we would like a new business card design to reflect our company. It can be a single-sided or two-sided card, but it is important that our contact information appears on the same side. I am attaching a copy of our old card and our new logo. If you need the logo in another format than the one I'm sending, please let me know. This is the information that we must have on our card, but not necessarily in any specific order:
1) Our logo
2) General Contractor
3) Derek Halvorsen, Owner
4) 482 Commerce Ridge Road, Ridgemont Falls, Westland 48210
5) Office: 256-384-7150
7) Fax: 256-384-7151
8) Cell: 256-619-7150
9) halvorsenconstruction@qrm.net
10) halvorsenconstruction.com (can be omitted if necessary)
Also, I will need files in a format that I can alter if any of the above information changes in the near future. Thank you in advance for your submissions!
Target Market(s)
Commercial and residential clients, architects, and subcontractors.
Industry/Entity Type
Business

```html
<!DOCTYPE html>
<html lang="en">
<head>
<meta charset="utf-8">
<title>Halvorsen Construction — Business Card</title>
<link href="https://fonts.googleapis.com/css2?family=Crimson+Text:wght@400;700&display=swap" rel="stylesheet">
<style>
  :root {
    --backdrop: #e9e7e3;
    --terracotta: #b96b67;
    --sky: #87c9ee;
    --ink: #1c1a20;
    --card-shadow: rgba(0, 0, 0, 0.18);
  }
  html, body {
    margin: 0;
    width: 1200px;
    height: 900px;
    overflow: hidden;
    background: var(--backdrop);
  }
  .canvas {
    position: relative;
    width: 1200px;
    height: 900px;
  }
  .business-card {
    position: absolute;
    left: 180px;
    top: 210px;
    width: 840px;
    height: 480px;
    overflow: hidden;
    background: var(--sky);
    box-shadow: 0 10px 30px var(--card-shadow);
    font-family: "Crimson Text", Georgia, serif;
    color: var(--ink);
  }
  .card-art {
    position: absolute;
    inset: 0;
  }
  .brand {
    position: absolute;
    left: 110px;
    top: 62px;
    display: flex;
    align-items: center;
    gap: 22px;
  }
  .brand-square {
    width: 78px;
    height: 78px;
    background: var(--ink);
  }
  .brand-name {
    font-size: 46px;
    font-weight: 700;
    letter-spacing: 0.5px;
    line-height: 1;
    color: var(--ink);
    white-space: nowrap;
  }
  .contact {
    position: absolute;
    left: 130px;
    top: 250px;
    font-size: 19px;
    line-height: 1.2;
    white-space: nowrap;
  }
  .contact-name {
    font-size: 24px;
    font-weight: 700;
    margin-bottom: 6px;
  }
  .contact p { margin: 0; }
  .contact .online { margin-top: 12px; }
</style>
</head>
<body>
<main class="canvas">
  <section class="business-card">
    <svg class="card-art" width="840" height="480" viewBox="0 0 840 480" aria-hidden="true">
      <polygon points="0,0 620,0 230,480 0,480" fill="var(--terracotta)"/>
      <g class="corner-stripes" stroke="var(--ink)" stroke-width="7">
        <line x1="0" y1="150" x2="60" y2="0"/>
        <line x1="0" y1="118" x2="47" y2="0"/>
        <line x1="0" y1="86" x2="34" y2="0"/>
        <line x1="0" y1="54" x2="21" y2="0"/>
        <line x1="840" y1="330" x2="780" y2="480"/>
        <line x1="840" y1="362" x2="793" y2="480"/>
        <line x1="840" y1="394" x2="806" y2="480"/>
        <line x1="840" y1="426" x2="819" y2="480"/>
      </g>
    </svg>

    <div class="brand">
      <div class="brand-square"></div>
      <div class="brand-name">Halvorsen Construction</div>
    </div>

    <div class="contact">
      <p class="contact-name">Derek Halvorsen</p>
      <p>General Contractor</p>
      <p>482 Commerce Ridge Road, Ridgemont Falls, Westland 48210</p>
      <p>Office: 256-384-7150</p>
      <p>Fax: 256-384-7151</p>
      <p>Cell: 256-619-7150</p>
      <p class="online">halvorsenconstruction@qrm.net</p>
      <p>www.halvorsenconstruction.com</p>
    </div>
  </section>
</main>
</body>
</html>
```